Floor Inspections and Consulting

We provide inspections and consulting services on various floor coverings, e.g. carpet, hardwood, etc. We also do expert witness work for attorneys due to floor covering failures. We current have a logo, just need it incorporated into a new design. I have examples of cards I have found on the internet that capture my attention and make a statement. I have included our original business card, which in my opinion is terrible, but it does have our logo on it.

```html
<!DOCTYPE html>
<html lang="en">
<head>
<meta charset="utf-8">
<title>Keystone Floor Inspections – Business Card</title>
<link href="https://fonts.googleapis.com/css2?family=Archivo:wght@400;700;900&family=Arimo:wght@400&display=swap" rel="stylesheet">
<style>
  :root {
    --stage: #3b3b3b;
    --card: #141414;
    --orange: #f29a10;
    --orange-deep: #ea7a12;
    --grey: #8c8c8c;
    --grey-light: #b9b9b9;
  }
  * { box-sizing: border-box; margin: 0; padding: 0; }
  html, body {
    width: 1200px; height: 1015px; overflow: hidden;
    background: var(--stage);
  }
  .card {
    position: absolute;
    width: 580px; height: 330px;
    background: var(--card);
    box-shadow: 0 12px 30px rgba(0,0,0,.45);
    overflow: hidden;
    font-family: "Archivo", sans-serif;
  }
  .card::after {
    content: ""; position: absolute; left: 0; right: 0; bottom: 0;
    height: 9px; background: var(--orange);
  }
  .card--front { left: 110px; top: 120px; }
  .card--back  { left: 510px; top: 555px; }

  /* front */
  .front-brand {
    position: absolute; left: 0; right: 0; top: 78px;
    text-align: center;
  }
  .brand-mark {
    display: inline-block; width: 26px; height: 26px;
    background: var(--orange); margin-bottom: 16px;
  }
  .brand-name {
    font-weight: 900; color: var(--orange);
    font-size: 27px; letter-spacing: .5px; line-height: 1.15;
    text-transform: uppercase;
  }
  .brand-tag {
    display: flex; align-items: center; justify-content: center; gap: 8px;
    color: var(--orange); font-weight: 700; font-size: 10px;
    letter-spacing: 1.5px; text-transform: uppercase; margin-top: 8px;
  }
  .brand-tag::before, .brand-tag::after {
    content: ""; width: 44px; height: 1px; background: var(--orange);
  }
  .front-claim {
    position: absolute; left: 0; right: 0; top: 238px;
    text-align: center; color: var(--grey-light);
    font-weight: 900; font-size: 16px; letter-spacing: .3px;
  }

  /* back */
  .back-brand {
    position: absolute; left: 40px; top: 112px; width: 250px;
    text-align: center;
  }
  .back-brand .brand-name { font-size: 22px; }
  .divider {
    position: absolute; left: 318px; top: 58px;
    width: 1px; height: 170px; background: #4a4a4a;
  }
  .contact {
    position: absolute; left: 345px; top: 70px;
  }
  .person {
    color: var(--orange-deep); font-weight: 900;
    font-size: 21px; text-transform: uppercase; margin-bottom: 18px;
  }
  .contact-list { list-style: none; }
  .contact-item {
    display: flex; align-items: center; gap: 10px;
    font-family: "Arimo", sans-serif; font-size: 14px;
    color: var(--grey); margin-bottom: 9px;
  }
  .contact-item svg { width: 17px; height: 17px; flex: none; }
</style>
</head>
<body>

<section class="card card--front" aria-label="Card front">
  <div class="front-brand">
    <span class="brand-mark"></span>
    <div class="brand-name">Keystone Floor<br>Inspections</div>
    <div class="brand-tag">Analysis &amp; Consulting</div>
  </div>
  <p class="front-claim">Certified Floor Covering Inspection &amp; Consulting</p>
</section>

<section class="card card--back" aria-label="Card back">
  <div class="back-brand">
    <span class="brand-mark"></span>
    <div class="brand-name">Keystone Floor<br>Inspections</div>
  </div>
  <div class="divider"></div>
  <div class="contact">
    <h1 class="person">Daniel Marlow</h1>
    <ul class="contact-list">
      <li class="contact-item">
        <svg viewBox="0 0 20 20" fill="none" stroke="#ea7a12" stroke-width="1.8">
          <rect x="1.5" y="1.5" width="17" height="17" rx="2"/>
          <path d="M6 5l2 0 1 3-1.5 1a6 6 0 0 0 3.5 3.5l1-1.5 3 1v2a1 1 0 0 1-1 1A9 9 0 0 1 5 6a1 1 0 0 1 1-1z" fill="#ea7a12" stroke="none"/>
        </svg>
        303-555-0147
      </li>
      <li class="contact-item">
        <svg viewBox="0 0 20 20">
          <rect x="1" y="4" width="18" height="12" fill="#ea7a12"/>
          <path d="M1 4l9 7 9-7" fill="none" stroke="#141414" stroke-width="1.5"/>
        </svg>
        daniel@keystonefloors.com
      </li>
      <li class="contact-item">
        <svg viewBox="0 0 20 20" fill="none" stroke="#ea7a12" stroke-width="1.6">
          <circle cx="10" cy="10" r="8.2"/>
          <ellipse cx="10" cy="10" rx="3.6" ry="8.2"/>
          <path d="M2 10h16M3.5 5.5h13M3.5 14.5h13"/>
        </svg>
        www.keystonefloors.com
      </li>
    </ul>
  </div>
</section>

</body>
</html>
```